I need a business card design for a new business based in South West Australia.
I specialize in residential window cleaning & general handyman maintenance.

Dale Marsh - 412 SILVER HAWK DETAILING
- Window Cleaning
- House Maintenance

```html
<!DOCTYPE html>
<html lang="en">
<head>
<meta charset="utf-8">
<title>412 Silver Hawk Detailing – Business Card</title>
<link rel="stylesheet" href="https://fonts.googleapis.com/css2?family=Jost:wght@500;600&family=Source+Sans+3:wght@400;600&display=swap">
<style>
  :root {
    --page-bg: #1c232c;
    --blue-deep: #0a5fae;
    --blue-bright: #1ab6ec;
    --green-main: #9bbb45;
    --green-light: #b4cd5a;
    --green-shadow: #8aab38;
    --white: #ffffff;
    --ink: #111111;
  }
  html, body {
    margin: 0;
    padding: 0;
    width: 1200px;
    height: 1200px;
    overflow: hidden;
    background: var(--page-bg);
  }
  .business-card {
    position: absolute;
    left: 80px;
    top: 290px;
    width: 1040px;
    height: 620px;
    overflow: hidden;
    font-family: "Source Sans 3", sans-serif;
  }
  .card-background {
    position: absolute;
    inset: 0;
  }
  .brand-mark {
    position: absolute;
    left: 90px;
    top: 95px;
    width: 230px;
    display: flex;
    flex-direction: column;
    align-items: center;
    gap: 16px;
  }
  .brand-mark__square {
    width: 56px;
    height: 56px;
    background: var(--white);
  }
  .brand-mark__name {
    font-family: "Jost", sans-serif;
    font-weight: 500;
    font-size: 28px;
    line-height: 1.15;
    color: var(--white);
    text-align: center;
  }
  .company-title {
    position: absolute;
    left: 435px;
    top: 40px;
    margin: 0;
    font-family: "Jost", sans-serif;
    font-weight: 500;
    font-size: 55px;
    line-height: 1.28;
    letter-spacing: 1px;
    color: var(--white);
  }
  .services {
    position: absolute;
    left: 440px;
    top: 205px;
    margin: 0;
    padding: 0;
    list-style: none;
    color: var(--white);
    font-size: 27px;
    font-weight: 600;
    letter-spacing: 0.5px;
  }
  .services li {
    display: flex;
    align-items: center;
    gap: 14px;
    padding: 10px 0;
  }
  .services li + li {
    border-top: 2px solid var(--white);
  }
  .services svg { width: 24px; height: 24px; fill: var(--white); }
  .contact-person {
    position: absolute;
    left: 72px;
    top: 395px;
  }
  .contact-person__name {
    margin: 0;
    font-weight: 600;
    font-size: 56px;
    line-height: 1.2;
    color: var(--ink);
  }
  .contact-line {
    display: flex;
    align-items: center;
    gap: 12px;
    font-size: 34px;
    font-weight: 600;
    color: var(--ink);
    margin: 4px 0 0;
  }
  .contact-line svg { width: 26px; height: 26px; fill: var(--ink); }
  .contact-details {
    position: absolute;
    left: 440px;
    top: 455px;
  }
  .contact-details .contact-line { margin-bottom: 14px; font-size: 31px; }
</style>
</head>
<body>
  <div class="business-card">
    <svg class="card-background" viewBox="0 0 1040 620" width="1040" height="620" aria-hidden="true">
      <defs>
        <radialGradient id="blue-glow" cx="0.27" cy="0.52" r="0.75">
          <stop offset="0" stop-color="var(--blue-bright)"/>
          <stop offset="0.55" stop-color="var(--blue-deep)"/>
          <stop offset="1" stop-color="var(--blue-deep)"/>
        </radialGradient>
        <linearGradient id="hill-sheen" x1="0" y1="0" x2="1" y2="1">
          <stop offset="0" stop-color="var(--green-shadow)"/>
          <stop offset="0.7" stop-color="var(--green-light)"/>
          <stop offset="1" stop-color="var(--green-main)"/>
        </linearGradient>
      </defs>
      <rect width="1040" height="620" fill="url(#blue-glow)"/>
      <path d="M0 350 Q330 320 675 355 Q860 320 1040 315 L1040 620 L0 620 Z" fill="var(--green-main)"/>
      <path d="M675 355 Q860 320 1040 315 L1040 445 Q900 370 675 355 Z" fill="url(#hill-sheen)"/>
      <path d="M0 350 Q330 320 675 355 Q860 320 1040 315" fill="none" stroke="var(--white)" stroke-width="6"/>
    </svg>

    <div class="brand-mark">
      <span class="brand-mark__square"></span>
      <span class="brand-mark__name">412 SILVER HAWK DETAILING</span>
    </div>

    <h1 class="company-title">412 SILVER HAWK<br>DETAILING</h1>

    <ul class="services">
      <li><svg viewBox="0 0 24 24"><path d="M12 2 1 12h3v10h6v-6h4v6h6V12h3z"/></svg>Window Cleaning</li>
      <li><svg viewBox="0 0 24 24"><path d="M12 2 1 12h3v10h6v-6h4v6h6V12h3z"/></svg>House Maintenance</li>
    </ul>

    <div class="contact-person">
      <p class="contact-person__name">Dale Marsh</p>
      <p class="contact-line">
        <svg viewBox="0 0 24 24"><path d="M6.6 10.8a15 15 0 0 0 6.6 6.6l2.2-2.2a1 1 0 0 1 1-.25 11.4 11.4 0 0 0 3.6.57 1 1 0 0 1 1 1V20a1 1 0 0 1-1 1A17 17 0 0 1 3 4a1 1 0 0 1 1-1h3.5a1 1 0 0 1 1 1c0 1.250.2 2.450.57 3.570a1 1 0 0 1-.25 1z"/></svg>
        043 00 555 12
      </p>
    </div>

    <div class="contact-details">
      <p class="contact-line">
        <svg viewBox="0 0 24 24"><path d="M12 2 1 12h3v10h6v-6h4v6h6V12h3z"/></svg>
        #00, Adress 01, Line 02
      </p>
      <p class="contact-line">
        <svg viewBox="0 0 24 24"><path d="M12 2a10 10 0 1 0 0 20 10 10 0 0 0 0-20zm6.9 6h-3a15 15 0 0 0-1.3-3.9A8 8 0 0 1 18.9 8zM12 4c.8 1.1 1.5 2.5 1.9 4h-3.8c.4-1.5 1.1-2.9 1.9-4zM4.3 14a8 8 0 0 1 0-4h3.4a16 16 0 0 0 0 4zm.8 2h3a15 15 0 0 0 1.3 3.9A8 8 0 0 1 5.1 16zm3-8h-3a8 8 0 0 1 4.3-3.9A15 15 0 0 0 8.1 8zM12 20c-.8-1.1-1.5-2.5-1.9-4h3.8c-.4 1.5-1.1 2.9-1.9 4zm2.3-6H9.7a14 14 0 0 1 0-4h4.6a14 14 0 0 1 0 4zm.3 5.9a15 15 0 0 0 1.3-3.9h3a8 8 0 0 1-4.3 3.9zm1.7-5.9a16 16 0 0 0 0-4h3.4a8 8 0 0 1 0 4z"/></svg>
        hello@silverhawkmail.com
      </p>
    </div>
  </div>
</body>
</html>
```